holloway paving service

Needs to have phone number 0418259730 and email markholloway@brightmail.com.au.
ABN 62318470915
name mark holloway

For all your concreting solutions
Excavation
Exposed & colour concrete
House & shed slabs
Driveways
Landing & steps

Contact Information for Business Card

ph 0418259730
email markholloway@brightmail.com.au.
ABN 62318470915
name mark holloway

```html
<!DOCTYPE html>
<html lang="en">
<head>
<meta charset="utf-8">
<title>Holloway Paving Service – Business Card</title>
<link rel="stylesheet" href="https://fonts.googleapis.com/css2?family=Roboto:wght@400;500;700&family=Roboto+Condensed:wght@700&display=swap">
<style>
  :root {
    --backdrop: #2f2f2f;
    --card-white: #f2f2f2;
    --brand-orange: #f26722;
    --divider-grey: #6e6e6e;
    --card-grey: #6d6d6d;
    --text-white: #ffffff;
  }
  * { margin: 0; padding: 0; box-sizing: border-box; }
  html, body {
    width: 1200px; height: 960px; overflow: hidden;
    background: var(--backdrop);
    font-family: "Roboto", Arial, sans-serif;
  }
  .stage { position: relative; width: 1200px; height: 960px; }

  .card {
    position: absolute;
    width: 600px; height: 342px;
    box-shadow: 0 3px 8px rgba(0,0,0,0.45);
    overflow: hidden;
  }
  .card--front { left: 322px; top: 110px; background: var(--card-white); }
  .card--back { left: 320px; top: 494px; background: var(--card-grey); }

  /* front: left brand area */
  .brand {
    position: absolute; left: 36px; top: 150px;
    display: flex; align-items: center; gap: 10px;
  }
  .brand__mark {
    width: 22px; height: 22px; background: var(--brand-orange);
  }
  .brand__text { display: flex; flex-direction: column; }
  .brand__name {
    color: var(--brand-orange);
    font-weight: 700; font-size: 14px; letter-spacing: 0.2px;
    white-space: nowrap;
  }
  .brand__phone {
    color: var(--brand-orange);
    font-weight: 500; font-size: 12px; letter-spacing: 1px;
    margin-top: 3px;
  }

  /* front: orange info panel */
  .info-panel {
    position: absolute; left: 323px; top: 0;
    width: 277px; height: 342px;
    background: var(--brand-orange);
  }
  .divider {
    position: absolute; left: 318px; top: 0;
    width: 3px; height: 342px;
    background: var(--divider-grey);
  }
  .info-panel__name {
    position: absolute; left: 30px; top: 56px;
    font-family: "Roboto Condensed", "Arial Narrow", sans-serif;
    font-weight: 700; font-size: 23px; color: var(--text-white);
    text-transform: uppercase;
  }
  .contact-list {
    position: absolute; left: 31px; top: 105px;
    list-style: none; color: var(--text-white); font-size: 14px;
  }
  .contact-list li {
    display: flex; align-items: center; gap: 7px;
    height: 19.5px;
  }
  .contact-list svg { width: 13px; height: 13px; fill: var(--text-white); flex: none; }
  .abn {
    position: absolute; left: 31px; top: 170px;
    color: var(--text-white); font-size: 14px;
  }
  .services {
    position: absolute; left: 31px; top: 195px;
    list-style: none; color: var(--text-white); font-size: 14px;
  }
  .services li { height: 18px; display: flex; align-items: center; gap: 7px; }
  .services li::before {
    content: ""; width: 6px; height: 6px;
    background: var(--text-white); transform: rotate(45deg);
  }

  /* back */
  .back-lockup {
    position: absolute; right: 34px; top: 232px;
    text-align: center; color: var(--text-white);
  }
  .back-lockup__name {
    font-weight: 700; font-size: 18px; text-transform: uppercase;
    letter-spacing: 0.3px; white-space: nowrap;
  }
  .back-lockup__phone {
    font-weight: 500; font-size: 15px; letter-spacing: 1.5px; margin-top: 6px;
  }
  .back-lockup__web {
    font-size: 14px; letter-spacing: 3.4px; margin-top: 4px;
  }
</style>
</head>
<body>
<main class="stage">

  <section class="card card--front" aria-label="Business card front">
    <div class="brand">
      <span class="brand__mark"></span>
      <div class="brand__text">
        <span class="brand__name">HOLLOWAY PAVING SERVICE</span>
        <span class="brand__phone">0418259730</span>
      </div>
    </div>

    <div class="divider"></div>

    <div class="info-panel">
      <h1 class="info-panel__name">Mark Holloway</h1>

      <ul class="contact-list">
        <li>
          <svg viewBox="0 0 24 24" aria-hidden="true"><path d="M6.6 10.8a15.2 15.2 0 0 0 6.6 6.6l2.2-2.2c.3-.3.7-.4 1-.2 1.1.4 2.3.6 3.6.6.6 0 1 .4 1 1V20c0 .6-.4 1-1 1A17 17 0 0 1 3 4c0-.6.4-1 1-1h3.5c.6 0 1 .4 1 1 0 1.3.2 2.5.6 3.6.1.3 0 .7-.2 1z"/></svg>
          0418259730
        </li>
        <li>
          <svg viewBox="0 0 24 24" aria-hidden="true"><path d="M2 5h20v14H2z M4 7v.5l8 5 8-5V7l-8 5z" fill-rule="evenodd"/></svg>
          markholloway@brightmail.com.au
        </li>
        <li>
          <svg viewBox="0 0 24 24" aria-hidden="true"><path d="M12 2a10 10 0 1 0 0 20 10 10 0 0 0 0-20zm-1 17.9A8 8 0 0 1 4.2 10L9 14.8v1c0 1.1.9 2 2 2zm6.9-2.5c-.3-.8-1-1.4-1.9-1.4h-1v-3c0-.6-.4-1-1-1H8v-2h2c.6 0 1-.4 1-1V7h2c1.1 0 2-.9 2-2v-.4a8 8 0 0 1 2.9 12.8z"/></svg>
          www.hollowaypaving.com.au
        </li>
      </ul>

      <p class="abn">ABN 62318470915</p>

      <ul class="services">
        <li>Excavation</li>
        <li>Exposed &amp; colour concrete</li>
        <li>House &amp; shed slabs</li>
        <li>Driveways</li>
        <li>Landing &amp; steps</li>
      </ul>
    </div>
  </section>

  <section class="card card--back" aria-label="Business card back">
    <div class="back-lockup">
      <p class="back-lockup__name">Holloway Paving Service</p>
      <p class="back-lockup__phone">0418259730</p>
      <p class="back-lockup__web">www.hollowaypaving.com.au</p>
    </div>
  </section>

</main>
</body>
</html>
```